Business Card - connecting 2 souls and beggining the journey of self discovery

Logo on the front
with tag line

On the back list of services and contact details

Seminars
workshops
Coaching
podcasts

Darren Whitlow
Health & Wellbeing Life Coach
0491 372 615
darren@brightcoreliving.example
brightcoreliving.example

Industry/Entity Type

Life Coaching

Contact Information for Business Card

I like the use of colour from the logo to be used. I'm not a fan of white.

Requirements
Must have
• My tagline: every path inward begins with you
Nice to have
• Use of colour that is in the mind body soul logo

```html
<!DOCTYPE html>
<html lang="en">
<head>
<meta charset="utf-8">
<title>Brightcore Living – Business Card</title>
<link href="https://fonts.googleapis.com/css2?family=Open+Sans:ital,wght@0,400;0,600;0,700;1,400&display=swap" rel="stylesheet">
<style>
  :root {
    --backdrop: #3a2620;
    --card: #ffffff;
    --coral: #f07062;
    --ink: #3f3f3f;
    --muted: #7a7a7a;
    --rule: #6d6d6d;
    --mark: #e9738c;
  }
  * { margin: 0; padding: 0; box-sizing: border-box; }
  html, body { width: 1200px; height: 1000px; overflow: hidden; }
  body {
    background: var(--backdrop);
    font-family: "Open Sans", Arial, sans-serif;
    position: relative;
  }
  .card {
    position: absolute;
    left: 384px;
    width: 425px;
    height: 242px;
    background: var(--card);
    box-shadow: 0 2px 6px rgba(0,0,0,0.35);
  }
  .card--contact { top: 231px; }
  .card--brand { top: 512px; }

  .identity {
    position: absolute;
    right: 264px;
    top: 87px;
    text-align: right;
  }
  .identity__name {
    color: var(--coral);
    font-weight: 700;
    font-size: 15px;
    line-height: 20px;
  }
  .identity__role {
    color: var(--ink);
    font-size: 13px;
    line-height: 18px;
  }
  .divider {
    position: absolute;
    left: 172px;
    top: 76px;
    width: 1px;
    height: 61px;
    background: var(--rule);
  }
  .contacts {
    position: absolute;
    left: 185px;
    top: 80px;
    list-style: none;
    color: var(--ink);
  }
  .contacts li {
    display: flex;
    align-items: center;
    gap: 7px;
    font-size: 13px;
    line-height: 18px;
    white-space: nowrap;
  }
  .contacts li.contacts__phone { font-size: 12px; }
  .contacts svg { width: 10px; height: 10px; flex: none; }

  .services {
    position: absolute;
    left: 14px;
    top: 195px;
    width: 398px;
    height: 32px;
    background: var(--coral);
    color: #fff;
    font-size: 13.5px;
    display: flex;
    align-items: center;
    justify-content: space-between;
    padding: 0 20px 0 22px;
  }

  .brand {
    position: absolute;
    left: 0;
    right: 0;
    top: 58px;
    text-align: center;
  }
  .brand__dot {
    display: block;
    margin: 0 auto 16px;
    width: 80px;
    height: 80px;
    border-radius: 50%;
    background: var(--mark);
  }
  .brand__name {
    color: var(--muted);
    font-size: 20px;
    font-weight: 400;
    line-height: 24px;
    letter-spacing: -0.3px;
  }
  .brand__tagline {
    color: var(--muted);
    font-style: italic;
    font-size: 12.5px;
    line-height: 16px;
  }
</style>
</head>
<body>
  <section class="card card--contact">
    <div class="identity">
      <p class="identity__name">Darren Whitlow</p>
      <p class="identity__role">Life Coach</p>
    </div>
    <div class="divider"></div>
    <ul class="contacts">
      <li class="contacts__phone">
        <svg viewBox="0 0 10 10" aria-hidden="true"><path fill="var(--coral)" d="M2 0.5 L3.6 0.5 L4.2 2.8 L3 3.6 Q4 5.8 6.3 7 L7.2 5.8 L9.5 6.4 L9.5 8 Q9.5 9.5 8 9.5 Q1 9 0.5 2 Q0.5 0.5 2 0.5Z"/></svg>
        0491 372 615
      </li>
      <li>
        <svg viewBox="0 0 10 10" aria-hidden="true"><rect x="0.5" y="2" width="9" height="6.5" fill="var(--coral)"/><path d="M1 2.5 L5 5.6 L9 2.5" stroke="#fff" stroke-width="0.9" fill="none"/></svg>
        darren@brightcoreliving.example
      </li>
      <li>
        <svg viewBox="0 0 10 10" aria-hidden="true"><circle cx="5" cy="5" r="4.3" fill="none" stroke="var(--coral)" stroke-width="1"/><ellipse cx="5" cy="5" rx="1.8" ry="4.3" fill="none" stroke="var(--coral)" stroke-width="0.9"/><path d="M0.7 5 H9.3 M1.5 2.8 H8.5 M1.5 7.2 H8.5" stroke="var(--coral)" stroke-width="0.8"/></svg>
        www.brightcoreliving.example
      </li>
    </ul>
    <div class="services">
      <span>Seminars</span><span>|</span><span>Workshops</span><span>|</span><span>Coaching</span><span>|</span><span>Podcasts</span>
    </div>
  </section>

  <section class="card card--brand">
    <div class="brand">
      <span class="brand__dot"></span>
      <p class="brand__name">Brightcore Living</p>
      <p class="brand__tagline">“ every path inward begins with you ”</p>
    </div>
  </section>
</body>
</html>
```